A website for a Maltese Law Firm

Our law firm needs a website to further its business. The site should have a simple yet effective design. We would need the following sections: About us, Practice Areas, About Malta, Contact. These should be further split as follows:

About us: Our firm, Our values, What others say, Offices

Practice Areas: Crimimal, Citizenship & Residence, Sovereign Patron Pathway, Criminal Defence, Civil Litigation, Arbitration and ADR, Commercial and Corporate, Media Law.

About Malta: just one section.

Contact: Just one section

We would also need a news feed at the front of the site to include latest news regarding our cases.

At the bottom we need a section for our Terms and a Privacy Statement.

Our logo is being attached.

Target Market(s)

All clients looking for legal assistance in Malta

Industry/Entity Type

Legal

Coding

Coded - Design and coding required

Number of Pages Required

1 page

Requirements
Must have
• It must be simple yet striking.

```html
<!DOCTYPE html>
<html lang="en">
<head>
<meta charset="utf-8">
<title>Zerafa &amp; Attard Advocates</title>
<link rel="stylesheet" href="https://fonts.googleapis.com/css2?family=Cinzel:wght@400;600;700&family=Lato:ital,wght@0,400;0,700;1,400&display=swap">
<style>
:root{
  --ink:#2b2d33;
  --dark:#2c2f36;
  --nav:#2e3138;
  --nav-active:#bfc0c2;
  --paper:#ffffff;
  --mist:#ececec;
  --band:#a9aaad;
  --foot-bar:#b8b9bc;
  --text:#333333;
  --btn-grey:#b9babd;
}
*{box-sizing:border-box;margin:0;padding:0}
html,body{width:1200px;height:2723px;overflow:hidden;background:var(--paper)}
body{font-family:"Lato",Arial,sans-serif;color:var(--text);position:relative}
section,header,footer,nav{position:absolute;left:0;width:1200px}

/* header */
.site-header{top:0;height:107px;background:var(--paper)}
.wordmark{position:absolute;display:flex;align-items:center;gap:12px;font-family:"Lato",Arial,sans-serif;font-weight:700;white-space:nowrap}
.wordmark__mark{flex:none;background:currentColor}
.site-header .wordmark{left:72px;top:32px;font-size:30px;line-height:40px;color:var(--ink)}
.site-header .wordmark__mark{width:26px;height:26px}
.header-contact{position:absolute;left:897px;top:22px;font-size:17px;font-weight:700;color:var(--ink)}
.header-contact div{display:flex;align-items:center;gap:10px;height:32px}
.icon-box{width:24px;height:24px;background:var(--ink);border-radius:4px;display:inline-flex;align-items:center;justify-content:center}

/* nav */
.main-nav{top:107px;height:45px;background:var(--nav)}
.main-nav ul{list-style:none;display:flex;margin-left:68px}
.main-nav li{font-family:"Cinzel",Georgia,serif;font-size:15px;color:#fff;height:45px;line-height:45px;padding:0 24px;border-right:1px solid #666a72;letter-spacing:.5px;white-space:nowrap}
.main-nav li.is-active{background:var(--nav-active);color:var(--ink)}

/* hero */
.hero{top:152px;height:425px;background:linear-gradient(100deg,#4a2e22 0%,#6b4330 35%,#5a3626 60%,#3e261c 100%)}
.hero__art{position:absolute;left:80px;top:0;width:520px;height:425px;background:radial-gradient(ellipse at 45% 55%,#9a7050 0%,#6e4a34 45%,transparent 75%)}
.hero__title{position:absolute;right:70px;top:140px;width:460px;text-align:right;font-family:"Cinzel",Georgia,serif;font-weight:400;font-size:28px;line-height:37px;color:#fff;letter-spacing:.5px}
.hero__btn{position:absolute;left:793px;top:271px;width:338px;height:50px;background:#6b6b6b;border:2px solid #d9d9d9;color:#fff;font-family:"Cinzel",Georgia,serif;font-size:20px;line-height:46px;text-align:center;letter-spacing:1px}
.hero__dots{position:absolute;left:1082px;top:344px;display:flex;gap:4px}
.hero__dots span{width:12px;height:3px;background:#999}
.hero__dots span.on{background:#fff}

/* welcome */
.welcome{top:577px;height:453px;background:var(--mist)}
.welcome__copy{position:absolute;left:70px;top:62px;width:680px}
.section-title{font-family:"Cinzel",Georgia,serif;font-weight:400;font-size:29px;color:var(--ink);letter-spacing:1px}
.welcome__lead{font-size:16px;line-height:24px;color:#222;margin-top:14px}
.welcome__body{font-size:13.5px;line-height:22px;color:#333;margin-top:14px}
.pill-btn{display:inline-flex;align-items:center;height:32px;background:var(--btn-grey);border:1px solid #777;border-radius:3px 16px 16px 3px;padding-left:10px;font-size:12px;font-weight:700;color:var(--ink);letter-spacing:.5px}
.pill-btn .pill-btn__go{width:32px;height:32px;border-radius:50%;background:var(--dark);margin-left:12px;margin-right:-1px;display:flex;align-items:center;justify-content:center}
.welcome__copy .pill-btn{margin-top:24px}
.eval{position:absolute;left:797px;top:63px;width:331px;height:325px;border:2px solid var(--ink);background:var(--mist);padding:22px 16px}
.eval h3{font-family:"Cinzel",Georgia,serif;font-weight:400;font-size:23px;color:var(--ink);letter-spacing:1px;margin-left:2px}
.field{background:#fff;border:1px solid #ccc;height:40px;font-size:12px;padding:10px;color:#444;margin-top:10px}
.eval .field:first-of-type{margin-top:22px}
.field--tall{height:76px}
.eval .pill-btn{margin-top:14px;font-size:14px;padding-left:14px;height:38px;border-radius:3px 19px 19px 3px}
.eval .pill-btn .pill-btn__go{width:38px;height:38px;margin-left:18px}

/* practice areas */
.practice{top:1030px;height:425px;background:var(--paper)}
.practice .section-title{position:absolute;top:58px;width:100%;text-align:center}
.area{position:absolute;top:123px;width:280px;text-align:center}
.area__icon{width:100px;height:100px;margin:0 auto;border:3px solid var(--ink);display:flex;align-items:center;justify-content:center;background:#fff}
.area__icon.is-hover{background:var(--dark)}
.area__name{font-family:"Cinzel",Georgia,serif;font-size:18px;color:var(--ink);margin-top:22px;white-space:nowrap}
.area__text{font-size:13px;line-height:18px;color:#333;margin-top:8px;padding:0 54px}
.area__more{font-size:15px;color:#333;margin-top:8px}
.carousel-arrow{position:absolute;top:218px}

/* case studies */
.cases{top:1455px;height:527px;background:var(--mist)}
.cases .section-title{position:absolute;top:56px;width:100%;text-align:center}
.case{position:absolute;top:120px;width:310px}
.case__frame{border:1px solid #c8c8c8;background:#fff;padding:7px;height:165px;position:relative}
.case__photo{width:100%;height:100%}
.case__date{position:absolute;left:14px;top:12px;width:48px;text-align:center;font-size:15px;font-weight:700}
.case__day{background:var(--dark);color:#fff;height:24px;line-height:24px}
.case__month{background:#fff;color:#333;height:22px;line-height:22px;font-weight:400;font-size:14px}
.case__title{font-size:14px;font-weight:700;color:#111;margin-top:14px}
.case__text{font-size:12.5px;line-height:19px;color:#333;margin-top:10px;padding-right:10px}
.case__more{font-size:12.5px;color:#333;margin-top:8px}
.cases .pill-btn{position:absolute;left:537px;top:450px}

/* testimonials */
.testimonials{top:1982px;height:300px;background:var(--paper)}
.testimonials .section-title{position:absolute;top:56px;width:100%;text-align:center}
.testimonial__photo{position:absolute;left:135px;top:118px;width:116px;height:118px}
.testimonial__quote{position:absolute;left:315px;top:114px;width:760px;font-size:13.5px;line-height:22px;font-style:italic;color:#333}
.testimonial__mark{position:absolute;font-family:Georgia,serif;font-size:60px;color:#e0e0e0;line-height:1}
.testimonial__name{position:absolute;left:307px;top:214px;font-family:"Cinzel",Georgia,serif;font-size:19px;color:#333;letter-spacing:1px}

/* call to action */
.cta{top:2282px;height:130px;background:var(--band)}
.cta__text{position:absolute;left:115px;top:28px;font-family:"Cinzel",Georgia,serif;font-size:29px;line-height:36px;color:#fff;letter-spacing:1px}
.cta__btn{position:absolute;left:844px;top:39px;width:224px;height:47px;background:var(--dark);border:2px solid #fff;color:#fff;font-size:24px;font-weight:700;text-align:center;line-height:43px}

/* footer */
.site-footer{top:2412px;height:266px;background:var(--dark);color:#fff}
.foot-head{position:absolute;top:38px;font-family:"Cinzel",Georgia,serif;font-size:17px;letter-spacing:1px;padding-bottom:8px;border-bottom:1px solid #555}
.quick-links{position:absolute;left:70px;top:82px;list-style:none;font-size:12px;font-weight:700}
.quick-links li{height:24.5px;display:flex;align-items:center;gap:8px}
.quick-links li::before{content:"";width:4px;height:4px;background:#fff;border-radius:50%}
.foot-map{position:absolute;left:303px;top:82px;width:258px;height:125px;background:linear-gradient(135deg,#e6e4dc,#d8d8cf 50%,#e9e6de);border:2px solid #fff}
.foot-contact{position:absolute;left:590px;top:82px;font-size:12px;font-weight:700;line-height:16px}
.foot-contact .row{display:flex;gap:14px;margin-bottom:9px;align-items:flex-start}
.foot-contact .row svg{flex:none;margin-top:1px}
.site-footer .wordmark{left:886px;top:92px;font-size:18px;line-height:24px;color:#fff;gap:8px}
.site-footer .wordmark__mark{width:14px;height:14px}
.socials{position:absolute;left:924px;top:148px;display:flex;gap:12px}
.socials span{width:32px;height:32px;border-radius:50%;background:#5d6068;border:2px solid #fff}
.copyright{position:absolute;left:0;top:2678px;width:1200px;height:45px;background:var(--foot-bar);font-size:12.5px;color:#222;line-height:45px}
.copyright__left{position:absolute;left:70px}
.copyright__right{position:absolute;right:70px}
</style>
</head>
<body>

<header class="site-header">
  <div class="wordmark"><span class="wordmark__mark"></span>Zerafa &amp; Attard Advocates</div>
  <div class="header-contact">
    <div><span class="icon-box"><svg width="12" height="16" viewBox="0 0 12 16"><rect x="1" y="1" width="10" height="14" rx="2" fill="none" stroke="#fff" stroke-width="1.6"/><circle cx="6" cy="12.5" r="1" fill="#fff"/></svg></span>555-014-2290</div>
    <div><span class="icon-box"><svg width="16" height="12" viewBox="0 0 16 12"><rect x="1" y="1" width="14" height="10" fill="none" stroke="#fff" stroke-width="1.5"/><path d="M1 1l7 6 7-6" fill="none" stroke="#fff" stroke-width="1.5"/></svg></span>info@zaadvocates.example</div>
  </div>
</header>

<nav class="main-nav">
  <ul>
    <li class="is-active">Home</li>
    <li>About Malta</li>
    <li>Practice Areas</li>
    <li>Our Firm</li>
    <li>Our Values</li>
    <li>What Others Say</li>
    <li>Contact Us</li>
  </ul>
</nav>

<section class="hero">
  <div class="hero__art" role="img" aria-label="Photograph of a wooden gavel resting on law books beside brass scales of justice"></div>
  <h1 class="hero__title">Realize Your Constitutional Right For Qualified Legal Help</h1>
  <div class="hero__btn">Get A Free Consultation</div>
  <div class="hero__dots"><span></span><span class="on"></span><span></span></div>
</section>

<section class="welcome">
  <div class="welcome__copy">
    <h2 class="section-title">Welcome To Zerafa &amp; Attard Advocates</h2>
    <p class="welcome__lead">Lorem ipsum dolor sit amet, consectetuer adipiscing elit, sed diam nonummy nibh euismod tincidunt ut laoreet dolore magna aliquam erat volutpat.</p>
    <p class="welcome__body">Lorem ipsum dolor sit amet, consectetur adipiscing elit. Sed vitae magna tellus. Aenean ante nunc, semper nec cursus non, rutrum ac eros. Vestibulum mattis justo ac dui bibendum consequat a ac ipsum. Praesent a arcu venenatis, auctor velit eu, suscipit libero. Quisque convallis, leo ac pharetra sagittis, ipsum arcu auctor urna, sit amet cursus risus augue in eros. Duis lacinia nisi vitae leo commodo, non finibus magna maximus. Sed posuere, neque eget bibendum pulvinar, ligula erat suscipit dolor, ut maximus arcu mi et tortor. Quisque imperdiet turpis et ligula mollis ultricies. Mauris lacinia rhoncus odio, at rutrum diam mollis eu. Quisque ut ipsum faucibus, tristique dui vitae, posuere orci.</p>
    <div class="pill-btn">READ MORE<span class="pill-btn__go"><svg width="10" height="12" viewBox="0 0 10 12"><path d="M3 1l5 5-5 5" fill="none" stroke="#fff" stroke-width="2"/></svg></span></div>
  </div>
  <form class="eval">
    <h3>Free Case Evaluation</h3>
    <div class="field">Name</div>
    <div class="field">Email</div>
    <div class="field field--tall">Message</div>
    <div class="pill-btn">SUBMIT<span class="pill-btn__go"><svg width="10" height="12" viewBox="0 0 10 12"><path d="M3 1l5 5-5 5" fill="none" stroke="#fff" stroke-width="2"/></svg></span></div>
  </form>
</section>

<section class="practice">
  <h2 class="section-title">Our Practice Areas</h2>
  <svg class="carousel-arrow" style="left:32px" width="16" height="56" viewBox="0 0 16 56"><path d="M14 2L2 28l12 26" fill="none" stroke="#555" stroke-width="1.5"/></svg>
  <svg class="carousel-arrow" style="left:1152px" width="16" height="56" viewBox="0 0 16 56"><path d="M2 2l12 26L2 54" fill="none" stroke="#555" stroke-width="1.5"/></svg>

  <div class="area" style="left:60px">
    <div class="area__icon"><svg width="56" height="40" viewBox="0 0 56 40"><circle cx="16" cy="24" r="10" fill="none" stroke="#2b2d33" stroke-width="5"/><circle cx="40" cy="24" r="10" fill="none" stroke="#2b2d33" stroke-width="5"/><path d="M22 10l12 0" stroke="#2b2d33" stroke-width="5"/><rect x="8" y="4" width="10" height="8" fill="#2b2d33"/><rect x="38" y="4" width="10" height="8" fill="#2b2d33"/></svg></div>
    <div class="area__name">Crimimal</div>
    <p class="area__text">Lorem ipsum dolor sit amet, consectetuer Lorem dolor sit amet, consectetuer</p>
    <div class="area__more">[+]</div>
  </div>
  <div class="area" style="left:319px">
    <div class="area__icon is-hover"><svg width="40" height="52" viewBox="0 0 40 52"><rect x="2" y="2" width="36" height="48" rx="3" fill="#fff"/><circle cx="20" cy="20" r="9" fill="none" stroke="#2c2f36" stroke-width="2"/><path d="M11 20h18M20 11v18M14 14c4 3 8 3 12 0M14 26c4-3 8-3 12 0" fill="none" stroke="#2c2f36" stroke-width="1.5"/><rect x="12" y="38" width="16" height="3" fill="#2c2f36"/></svg></div>
    <div class="area__name">Citizenship &amp; Residence</div>
    <p class="area__text">Lorem ipsum dolor sit amet, consectetuer Lorem dolor sit amet, consectetuer</p>
    <div class="area__more">[+]</div>
  </div>
  <div class="area" style="left:588px">
    <div class="area__icon"><svg width="58" height="50" viewBox="0 0 58 50"><circle cx="29" cy="12" r="8" fill="#2b2d33"/><path d="M15 40c0-10 6-16 14-16s14 6 14 16z" fill="#2b2d33"/><rect x="13" y="26" width="32" height="14" rx="2" fill="#fff" stroke="#2b2d33" stroke-width="2"/><path d="M18 31h22M18 35h16" stroke="#2b2d33" stroke-width="2"/><path d="M2 16h8M2 22h8M48 16h8M48 22h8M2 44h54" stroke="#2b2d33" stroke-width="2"/></svg></div>
    <div class="area__name">Criminal Defence</div>
    <p class="area__text">Lorem ipsum dolor sit amet, consectetuer Lorem dolor sit amet, consectetuer</p>
    <div class="area__more">[+]</div>
  </div>
  <div class="area" style="left:862px">
    <div class="area__icon"><svg width="54" height="50" viewBox="0 0 54 50"><g transform="rotate(-40 27 20)"><rect x="16" y="6" width="24" height="12" rx="2" fill="#2b2d33"/><rect x="25" y="18" width="6" height="26" fill="#2b2d33"/></g><rect x="2" y="40" width="26" height="6" fill="#2b2d33"/></svg></div>
    <div class="area__name">Civil Litigation</div>
    <p class="area__text">Lorem ipsum dolor sit amet, consectetuer Lorem dolor sit amet, consectetuer</p>
    <div class="area__more">[+]</div>
  </div>
</section>

<section class="cases">
  <h2 class="section-title">Case Studies</h2>
  <article class="case" style="left:70px">
    <div class="case__frame"><div class="case__photo" role="img" aria-label="Photograph of rows of leather-bound law books" style="background:linear-gradient(90deg,#5a2a18,#a0743a 30%,#6d3a1e 55%,#b08848 80%,#4e2414)"></div>
      <div class="case__date"><div class="case__day">06</div><div class="case__month">Jun</div></div></div>
    <h3 class="case__title">Lorem Ipsum Dolor Sit Amet &nbsp;Consectetur</h3>
    <p class="case__text">Lorem ipsum dolor sit amet, consectetur adipiscing elit. Sed vitae magna tellus. Aenean ante nunc, semper nec cursus non, rutrum ac eros.</p>
    <div class="case__more">Read More ››</div>
  </article>
  <article class="case" style="left:445px">
    <div class="case__frame"><div class="case__photo" role="img" aria-label="Photograph of a courtroom with a defendant in handcuffs" style="background:linear-gradient(90deg,#6a3a22,#8e5a34 35%,#3a3a3e 65%,#2a2a2e)"></div>
      <div class="case__date"><div class="case__day">06</div><div class="case__month">Jun</div></div></div>
    <h3 class="case__title">Lorem Ipsum Dolor Sit Amet &nbsp;Consectetur</h3>
    <p class="case__text">Lorem ipsum dolor sit amet, consectetur adipiscing elit. Sed vitae magna tellus. Aenean ante nunc, semper nec cursus non, rutrum ac eros.</p>
    <div class="case__more">Read More ››</div>
  </article>
  <article class="case" style="left:820px">
    <div class="case__frame"><div class="case__photo" role="img" aria-label="Photograph of a hand signing a legal document" style="background:linear-gradient(120deg,#2a2a2e,#55565a 35%,#e8e6e2 60%,#cfcac4)"></div>
      <div class="case__date"><div class="case__day">07</div><div class="case__month">Jun</div></div></div>
    <h3 class="case__title">Lorem Ipsum Dolor Sit Amet &nbsp;Consectetur</h3>
    <p class="case__text">Lorem ipsum dolor sit amet, consectetur adipiscing elit. Sed vitae magna tellus. Aenean ante nunc, semper nec cursus non, rutrum ac eros.</p>
    <div class="case__more">Read More ››</div>
  </article>
  <div class="pill-btn">VIEW ALL<span class="pill-btn__go"><svg width="10" height="12" viewBox="0 0 10 12"><path d="M3 1l5 5-5 5" fill="none" stroke="#fff" stroke-width="2"/></svg></span></div>
</section>

<section class="testimonials">
  <h2 class="section-title">Client Testimonials</h2>
  <svg class="carousel-arrow" style="left:32px;top:142px" width="16" height="56" viewBox="0 0 16 56"><path d="M14 2L2 28l12 26" fill="none" stroke="#555" stroke-width="1.5"/></svg>
  <svg class="carousel-arrow" style="left:1152px;top:142px" width="16" height="56" viewBox="0 0 16 56"><path d="M2 2l12 26L2 54" fill="none" stroke="#555" stroke-width="1.5"/></svg>
  <div class="testimonial__photo" role="img" aria-label="Portrait photograph of the client" style="background:linear-gradient(180deg,#dfe3e8,#b7bcc4 55%,#3c4250)"></div>
  <span class="testimonial__mark" style="left:305px;top:100px">“</span>
  <p class="testimonial__quote">&nbsp;&nbsp;&nbsp;&nbsp;&nbsp;Lorem ipsum dolor sit amet, consectetuer adipiscing elit, sed diam nonummy nibh euismod tincidunt ut laoreet dolore magna aliquam erat volutpat. Ut wisi enim ad minim veniam, quis nostrud exerci iriure dolor in Lorem ipsum dolor sit amet, consectetuer adipiscing elit, sed diam nonummy nibh euismod tincidunt ut laoreet dolore magna aliquam erat volutpat. Ut wisi enim ad minim veniam, quis nostrud exerci iriure dolo.</p>
  <span class="testimonial__mark" style="left:538px;top:180px">”</span>
  <div class="testimonial__name">- Daniel Moreno</div>
</section>

<section class="cta">
  <div class="cta__text">For Any Legal Problem, We Can Help You<br>Anytime take An Appointment Now</div>
  <div class="cta__btn">CONTACT US</div>
</section>

<footer class="site-footer">
  <div class="foot-head" style="left:67px;width:140px">Quick Links</div>
  <ul class="quick-links">
    <li>Home</li><li>About Malta</li><li>Practice Areas</li><li>Our Firm</li><li>Our Values</li><li>What Others Say</li><li>Contact Us</li>
  </ul>
  <div class="foot-head" style="left:301px;width:490px">Contact Details</div>
  <div class="foot-map" role="img" aria-label="Street map showing the office location"></div>
  <div class="foot-contact">
    <div class="row"><svg width="12" height="16" viewBox="0 0 12 16"><path d="M6 15S1 9 1 6a5 5 0 0110 0c0 3-5 9-5 9z" fill="#fff"/><circle cx="6" cy="6" r="2" fill="#2c2f36"/></svg><div>Zerafa &amp; Attard Advocates<br>12/4, Harbour Lane, Valletta<br>88, Olive Grove Street, Birkirkara</div></div>
    <div class="row"><svg width="14" height="14" viewBox="0 0 14 14"><path d="M3 1l3 3-2 2c1 2 2 3 4 4l2-2 3 3-2 2C6 13 1 8 1 3z" fill="#fff"/></svg><div>555-014-229</div></div>
    <div class="row"><svg width="14" height="14" viewBox="0 0 14 14"><rect x="3" y="1" width="8" height="4" fill="#fff"/><rect x="1" y="5" width="12" height="6" rx="1" fill="#fff"/><rect x="3" y="9" width="8" height="4" fill="#fff" stroke="#2c2f36"/></svg><div>555-014-229</div></div>
    <div class="row"><svg width="14" height="12" viewBox="0 0 14 12"><rect x="1" y="1" width="12" height="10" fill="#fff"/><path d="M1 1l6 5 6-5" fill="none" stroke="#2c2f36" stroke-width="1.2"/></svg><div>info@zaadvocates.example</div></div>
  </div>
  <div class="wordmark"><span class="wordmark__mark"></span>Zerafa &amp; Attard Advocates</div>
  <div class="socials"><span></span><span></span><span></span><span></span></div>
</footer>

<div class="copyright">
  <span class="copyright__left">Copyright © 2016 <b>Zerafa &amp; Attard Advocates</b>. All Rights Reserved.</span>
  <span class="copyright__right">Terms &amp; Conditions &nbsp;|&nbsp; Privacy Policy &nbsp;|&nbsp; Disclaimer</span>
</div>

</body>
</html>
```